BOLD & MINIMALIST DESIGN NEEDED

We want a very bold but minimalistic business card design that is impactful and utilizes both sides of the business card. Our current logo is included for your use.

We want bold fonts and good use of negative space. We don't want the logo to overpower the design.

Target Market(s)

Professionals who are building new commercial buildings.

Industry/Entity Type

Construction

Contact Information for Business Card

Name, Title, email, office phone, cell phone, website

Font styles to use
Serif
Sans Serif

Requirements
Must have
• Bold design!

```html
<!DOCTYPE html>
<html lang="en">
<head>
<meta charset="utf-8">
<title>Ridgeline Design + Build — Business Card</title>
<link href="https://fonts.googleapis.com/css2?family=Montserrat:wght@400;500;800&display=swap" rel="stylesheet">
<style>
  :root {
    --green: #7dc242;
    --green-dark: #3f7d34;
    --green-light: #dcefc6;
    --ink: #111111;
    --text: #2a2a2a;
    --card: #ffffff;
    --stage: #e6e7e4;
  }
  * { box-sizing: border-box; margin: 0; padding: 0; }
  html, body { width: 1200px; height: 900px; overflow: hidden; }
  body {
    background: var(--stage);
    font-family: "Montserrat", sans-serif;
    position: relative;
  }
  .card {
    position: absolute;
    left: 250px;
    width: 700px;
    height: 400px;
    border-radius: 24px;
    overflow: hidden;
    background: var(--card);
    box-shadow: 0 6px 18px rgba(0,0,0,.12);
  }
  .card--back { top: 40px; }
  .card--front { top: 460px; }

  .pattern-field {
    position: absolute;
    inset: 0;
    background: linear-gradient(100deg, var(--green-light) 0%, #9fd36a 35%, var(--green) 55%, var(--green-dark) 100%);
  }

  .brand {
    position: absolute;
    left: 70px;
    top: 140px;
    display: flex;
    align-items: center;
    gap: 14px;
  }
  .brand__mark {
    width: 26px;
    height: 26px;
    background: var(--green);
  }
  .brand__name {
    font-weight: 800;
    color: var(--ink);
    font-size: 34px;
    line-height: 1.05;
    letter-spacing: .5px;
  }
  .brand__name span { display: block; font-size: 17px; letter-spacing: 4px; }

  .divider {
    position: absolute;
    left: 395px;
    top: 70px;
    width: 2px;
    height: 200px;
    background: var(--green);
  }

  .contact {
    position: absolute;
    left: 420px;
    top: 52px;
    color: var(--text);
  }
  .contact__name {
    font-weight: 800;
    color: var(--green);
    font-size: 30px;
    letter-spacing: 1px;
    line-height: 1;
  }
  .contact__title {
    font-size: 14px;
    font-weight: 500;
    letter-spacing: 1px;
    margin-top: 6px;
  }
  .contact__address {
    font-size: 14px;
    line-height: 1.45;
    margin-top: 14px;
  }
  .contact__list {
    list-style: none;
    margin-top: 12px;
    font-size: 14px;
    line-height: 1.6;
  }
  .contact__list li { display: flex; align-items: center; gap: 9px; }
  .contact__list svg { width: 14px; height: 14px; fill: var(--green); flex: none; }

  .swoosh {
    position: absolute;
    left: 0;
    bottom: 0;
    width: 700px;
    height: 400px;
  }
</style>
</head>
<body>

  <section class="card card--back" aria-label="Card back">
    <div class="pattern-field" role="img" aria-label="Repeating brand-mark pattern in green gradient"></div>
  </section>

  <section class="card card--front" aria-label="Card front">
    <svg class="swoosh" viewBox="0 0 700 400" aria-hidden="true">
      <path d="M0,352 C250,322 460,352 700,238 L700,250 C460,362 250,336 0,364 Z" fill="var(--ink)"/>
      <path d="M0,372 C250,344 460,372 700,262 L700,400 L0,400 Z" fill="var(--green)"/>
    </svg>

    <div class="brand">
      <div class="brand__mark"></div>
      <div class="brand__name">RIDGELINE<span>DESIGN + BUILD</span></div>
    </div>

    <div class="divider"></div>

    <div class="contact">
      <h1 class="contact__name">MARCUS VELL</h1>
      <p class="contact__title">OWNER-CEO</p>
      <p class="contact__address">Your address, City<br>State, Zip 1234</p>
      <ul class="contact__list">
        <li><svg viewBox="0 0 24 24"><path d="M6.6 10.8a15 15 0 0 0 6.6 6.6l2.2-2.2c.3-.3.7-.4 1-.2 1.1.4 2.3.6 3.6.6.6 0 1 .4 1 1V20c0 .6-.4 1-1 1A17 17 0 0 1 3 4c0-.6.4-1 1-1h3.5c.6 0 1 .4 1 1 0 1.3.2 2.5.6 3.6.1.3 0 .7-.2 1z"/></svg>123 456 789</li>
        <li><svg viewBox="0 0 24 24"><path d="M7 1h10a2 2 0 0 1 2 2v18a2 2 0 0 1-2 2H7a2 2 0 0 1-2-2V3a2 2 0 0 1 2-2zm0 3v14h10V4zm5 15.5a1 1 0 1 0 0 2 1 1 0 0 0 0-2z"/></svg>123 456 789</li>
        <li><svg viewBox="0 0 24 24"><path d="M2 5h20v14H2zm2 2v.5l8 5 8-5V7zm0 2.8V17h16V9.8l-8 5z"/></svg>info@yourmail.com</li>
        <li><svg viewBox="0 0 24 24"><path d="M12 2a10 10 0 1 0 0 20 10 10 0 0 0 0-20zm6.9 9h-3a15 15 0 0 0-1.3-5.6A8 8 0 0 1 18.9 11zM12 4c.9 1.2 1.8 3.6 1.9 7h-3.8c.1-3.4 1-5.8 1.9-7zM9.4 5.4A15 15 0 0 0 8.1 11h-3a8 8 0 0 1 4.3-5.6zM5.1 13h3a15 15 0 0 0 1.3 5.6A8 8 0 0 1 5.1 13zM12 20c-.9-1.2-1.8-3.6-1.9-7h3.8c-.1 3.4-1 5.8-1.9 7zm2.6-1.4a15 15 0 0 0 1.3-5.6h3a8 8 0 0 1-4.3 5.6z"/></svg>www.yourwebsite.com</li>
      </ul>
    </div>
  </section>

</body>
</html>
```